TK Homes - Stone Dorf Design

Looking for a double sides design, 1 side for my realestate and the other for home building. ( TK Homes on 1 side, Stone Dorf card on the other Side
Side 1 - Marek Tove ~ Vox Realty logo and Company ( the Property quarter )
Marek Tove
Marek@Marektove.example
IG - Marek_Bzq_Realtor
FB - marekt
Cell - 5558130467
3847 61 St Nw

Side 2
Marek Tove
5558130467
IG - Stonedorf_Bzq
Stonedorfdev@mailbox.example

Target Market(s)

Home buyers/ sellers

Industry/Entity Type

Home builders - Realestate

Contact Information for Business Card

Above

Requirements
Must have
• Black OR White background - my information -

```html
<!DOCTYPE html>
<html lang="en">
<head>
<meta charset="utf-8">
<title>Stone Dorf Design and TK Homes business cards</title>
<link rel="stylesheet" href="https://fonts.googleapis.com/css2?family=Tinos:wght@400;700&display=swap">
<style>
  :root {
    --page: #232323;
    --card: #1f1f22;
    --blue: #0b74c4;
    --red: #e0483a;
    --white: #ffffff;
    --serif: "Tinos", "Times New Roman", serif;
  }
  * { box-sizing: border-box; margin: 0; padding: 0; }
  html, body { width: 1200px; height: 780px; overflow: hidden; background: var(--page); }
  .stage {
    width: 1200px; height: 780px;
    display: flex; align-items: center; justify-content: center; gap: 40px;
  }
  .card {
    position: relative;
    width: 550px; height: 314px;
    background: var(--card);
    border-bottom: 5px solid var(--red);
    font-family: var(--serif);
    color: var(--white);
  }
  .card__brand {
    position: absolute; left: 0; top: 0; width: 250px; height: 100%;
    display: flex; align-items: center; justify-content: center;
  }
  .brand-name {
    font-family: var(--serif); font-weight: 700; color: var(--blue);
    font-size: 40px; line-height: 1; text-align: center; letter-spacing: 1px;
  }
  .card__divider {
    position: absolute; left: 262px; top: 48px; width: 2px; height: 190px;
    background: var(--white);
  }
  .card__details { position: absolute; left: 300px; top: 54px; }
  .person-name { font-weight: 700; font-size: 30px; line-height: 1; }
  .person-name__first { color: var(--blue); }
  .person-name__last { color: var(--red); }
  .person-role { font-weight: 700; font-size: 15px; margin: 4px 0 14px 10px; }
  .contact-list { list-style: none; }
  .contact-list li {
    display: flex; align-items: center; gap: 7px;
    font-size: 14px; line-height: 19px; white-space: nowrap;
  }
  .contact-icon { width: 12px; height: 12px; flex: none; }
  .card__address {
    position: absolute; right: 70px; bottom: 34px; font-size: 15px;
  }
</style>
</head>
<body>
<main class="stage">

  <section class="card card--builder" aria-label="Stone Dorf Design business card">
    <div class="card__brand">
      <span class="brand-name">Stone Dorf</span>
    </div>
    <div class="card__divider"></div>
    <div class="card__details">
      <h1 class="person-name"><span class="person-name__first">Marek</span> <span class="person-name__last">Tove</span></h1>
      <p class="person-role">Director</p>
      <ul class="contact-list">
        <li>
          <svg class="contact-icon" viewBox="0 0 12 12"><path fill="#0b74c4" d="M2.2 0.8l2 0 0.6 2.6-1.2 0.9c0.6 1.4 1.6 2.4 3 3l0.9-1.2 2.6 0.6 0 2c0 0.7-0.6 1.3-1.3 1.2C4.4 9.6 2.4 7.6 1 2.1 0.9 1.4 1.5 0.8 2.2 0.8z"/></svg>
          <span>5558130467</span>
        </li>
        <li>
          <svg class="contact-icon" viewBox="0 0 12 12"><rect x="1" y="1" width="10" height="10" rx="2" fill="none" stroke="#0b74c4" stroke-width="1.6"/></svg>
          <span>Stonedorf_Bzq</span>
        </li>
        <li>
          <svg class="contact-icon" viewBox="0 0 12 12"><rect x="0.5" y="2" width="11" height="8" fill="#0b74c4"/><path d="M0.5 2l5.5 4.5 5.5-4.5" fill="none" stroke="#1f1f22" stroke-width="1"/></svg>
          <span>Stonedorfdev@mailbox.example</span>
        </li>
      </ul>
    </div>
  </section>

  <section class="card card--realty" aria-label="TK Homes business card">
    <div class="card__brand">
      <span class="brand-name">Marek Tove</span>
    </div>
    <div class="card__divider"></div>
    <div class="card__details">
      <h1 class="person-name"><span class="person-name__first">Marek</span> <span class="person-name__last">Tove</span></h1>
      <p class="person-role">Director</p>
      <ul class="contact-list">
        <li>
          <svg class="contact-icon" viewBox="0 0 12 12"><path fill="#0b74c4" d="M2.2 0.8l2 0 0.6 2.6-1.2 0.9c0.6 1.4 1.6 2.4 3 3l0.9-1.2 2.6 0.6 0 2c0 0.7-0.6 1.3-1.3 1.2C4.4 9.6 2.4 7.6 1 2.1 0.9 1.4 1.5 0.8 2.2 0.8z"/></svg>
          <span>5558130467</span>
        </li>
        <li>
          <svg class="contact-icon" viewBox="0 0 12 12"><circle cx="6" cy="6" r="5.5" fill="#0b74c4"/></svg>
          <span>marekt</span>
        </li>
        <li>
          <svg class="contact-icon" viewBox="0 0 12 12"><rect x="1" y="1" width="10" height="10" rx="2" fill="none" stroke="#0b74c4" stroke-width="1.6"/></svg>
          <span>Marek_Bzq_Realtor</span>
        </li>
        <li>
          <svg class="contact-icon" viewBox="0 0 12 12"><rect x="0.5" y="2" width="11" height="8" fill="#0b74c4"/><path d="M0.5 2l5.5 4.5 5.5-4.5" fill="none" stroke="#1f1f22" stroke-width="1"/></svg>
          <span>Marek@Marektove.example</span>
        </li>
        <li>
          <svg class="contact-icon" viewBox="0 0 12 12"><g fill="none" stroke="#0b74c4" stroke-width="1"><circle cx="6" cy="6" r="5.2"/><ellipse cx="6" cy="6" rx="2.3" ry="5.2"/><path d="M0.8 6h10.4M1.6 3.3h8.8M1.6 8.7h8.8"/></g></svg>
          <span>www.marektove.example</span>
        </li>
      </ul>
    </div>
    <p class="card__address">3847 61 St Nw</p>
  </section>

</main>
</body>
</html>
```